Disability Magazine – Cover + Full Inside Layout

About the Publication

Our magazine is a quarterly, high‑impact publication that celebrates the lives, achievements, and everyday experiences of people with disabilities. It aims to inform, inspire, and advocate for accessibility, inclusion, and empowerment across all communities.

Target Audience

Adults (18‑65) with visible or invisible disabilities
Caregivers, family members, and allies
Professionals in health, education, policy, and design fields
Advocates and NGOs focused on accessibility

Project Goals

Visually compelling cover that instantly signals the magazine’s inclusive mission.
Consistent, readable interior layout for feature articles, interviews, photo essays, and resource guides.
Design that works both in print (A4, 300 dpi) and digitally (PDF/online flipbook).

```html
<!DOCTYPE html>
<html lang="en">
<head>
<meta charset="utf-8">
<title>Athlete – Sport Magazine Spreads</title>
<link href="https://fonts.googleapis.com/css2?family=Anton&family=Inter:wght@400;600&display=swap" rel="stylesheet">
<style>
:root{
  --board:#333333;
  --paper:#ffffff;
  --ink:#231f20;
  --lime:#cdf76b;
  --cover-red:#d42a3c;
  --muted:#555;
}
*{margin:0;padding:0;box-sizing:border-box}
html,body{width:876px;height:1200px;overflow:hidden;background:var(--board)}
.board{position:relative;width:876px;height:1200px}
.page{position:absolute;width:180px;height:255px;background:var(--paper);overflow:hidden;color:var(--ink)}
.abs{position:absolute}
.head{font-family:"Anton",sans-serif;font-weight:400;text-transform:uppercase;line-height:1.05;color:var(--ink);letter-spacing:0;white-space:nowrap}
.ital{font-style:italic}
.q{font-size:5.4px}
.body{font-family:"Inter",sans-serif;font-size:2.4px;line-height:1.55;color:var(--muted);text-align:justify}
.tiny{font-family:"Anton",sans-serif;font-size:3px;line-height:1.2;text-transform:uppercase;color:var(--ink);white-space:nowrap}
.rule{position:absolute;height:2px;background:var(--lime)}
.photo{position:absolute}
.foot{position:absolute;left:9px;right:25px;bottom:9px;height:2px;background:var(--lime)}
.folio{position:absolute;right:9px;bottom:9px;width:16px;height:15px;background:var(--lime);font-family:"Anton",sans-serif;font-style:italic;font-size:5px;display:flex;align-items:center;justify-content:center;color:var(--ink)}
.lime{color:var(--lime)}
.white{color:#fff}
.toc-num{font-family:"Anton",sans-serif;font-style:italic;font-size:11px;line-height:1;color:var(--ink)}
.toc-item{position:absolute;display:flex;gap:4px;width:82px}
.toc-title{font-family:"Anton",sans-serif;font-size:4.6px;line-height:1.1;text-transform:uppercase;white-space:nowrap}
.toc-desc{font-family:"Inter",sans-serif;font-size:2.2px;line-height:1.4;color:var(--muted);margin-top:1.5px}
.staff{position:absolute;left:0;width:180px;display:flex;align-items:center}
.staff .role{width:87px;text-align:right;font-family:"Anton",sans-serif;font-style:italic;font-size:3px;text-transform:uppercase;color:var(--ink)}
.staff .name{margin-left:7px;font-family:"Anton",sans-serif;font-size:6.4px;text-transform:uppercase}
.icon-box{position:absolute;width:10px;height:10px;background:var(--lime);display:flex;align-items:center;justify-content:center}
</style>
</head>
<body>
<main class="board">

<section class="page cover" style="left:48px;top:44px;background:var(--cover-red)">
  <div class="photo" role="img" aria-label="Sprinter with a running prosthesis leaping forward on a red textured background" style="inset:0;background:radial-gradient(ellipse 40% 55% at 40% 55%,rgba(40,30,30,.35),transparent 70%),radial-gradient(ellipse at 45% 55%,#c43340 0%,#d42a3c 45%,#bd1f2e 100%)"></div>
  <div class="tiny white abs" style="left:0;right:0;top:9px;text-align:center;font-size:5px;letter-spacing:.6px;font-family:Inter,sans-serif">SPORT MAGAZINE</div>
  <div class="head lime abs" style="left:0;right:0;top:16px;text-align:center;font-size:44px;line-height:1;transform:scaleY(1.12);transform-origin:top;letter-spacing:-1px">ATHLETE</div>
  <div class="tiny white abs ital" style="right:14px;top:70px;font-size:4px">ISSUE 24 &nbsp;JAN 2026</div>
  <div class="head white abs" style="right:9px;top:97px;text-align:right;font-size:13px;line-height:1">THE FUTURE<br>OF SPORTS</div>
  <div class="tiny white abs ital" style="right:9px;top:127px;text-align:right;font-size:3.2px">INNOVATING PERFORMANCE &amp;<br>BREAKING RECORDS</div>
  <div class="tiny white abs" style="left:21px;top:184px;font-size:4.4px;letter-spacing:.6px;font-family:Inter,sans-serif">EXCLUSIVE INTERVIEW</div>
  <div class="head white abs ital" style="left:17px;top:192px;font-size:19px;line-height:1.05">INSIDE THE MIND<br><span style="padding-left:32px">OF A CHAMPION</span></div>
  <div class="head abs" style="right:19px;top:235px;background:var(--lime);font-size:7px;padding:1px 3px">WITH NAME HERE</div>
</section>

<section class="page toc" style="left:244px;top:44px">
  <div class="head abs" style="left:0;right:0;top:8px;text-align:center;font-size:19px">TABLE OF CONTENT</div>
  <div class="rule" style="left:9px;right:9px;top:33px"></div>
  <div class="photo" role="img" aria-label="Three wheelchair athletes smiling on a blue indoor court" style="left:9px;top:44px;width:162px;height:104px;background:radial-gradient(ellipse 18% 30% at 50% 35%,#8c8a86,transparent 70%),radial-gradient(ellipse 14% 28% at 25% 40%,#d8c27a,transparent 70%),radial-gradient(ellipse 14% 28% at 75% 45%,#3e5fa0,transparent 70%),linear-gradient(180deg,#2f2c24 0%,#5e5744 35%,#4fa6c9 72%,#5bb8d8 100%)"></div>
  <div class="toc-item" style="left:9px;top:162px"><span class="toc-num">05</span><div><div class="toc-title">Feature Story:<br>The Future of Sports</div><div class="toc-desc">A look at innovation in sports technology and training</div></div></div>
  <div class="toc-item" style="left:96px;top:162px"><span class="toc-num">07</span><div><div class="toc-title">Interview: Inside the<br>Mind of a Champion</div><div class="toc-desc">Exclusive talk with Leona Marsh on excelling at the top level</div></div></div>
  <div class="toc-item" style="left:9px;top:193px"><span class="toc-num">09</span><div><div class="toc-title">Sport Tips:<br>Train Like a Pro</div><div class="toc-desc">Expert tips from elite coaches and nutritionists on workouts</div></div></div>
  <div class="toc-item" style="left:96px;top:193px"><span class="toc-num">11</span><div><div class="toc-title">Technology: Super<br>Shoe Innovations</div><div class="toc-desc">Athlete gear and equipment to boost performance and prevent injuries</div></div></div>
  <div class="toc-item" style="left:9px;top:224px"><span class="toc-num">13</span><div><div class="toc-title">Upcoming Events:<br>Sports Calendar 2024</div><div class="toc-desc">A guide to major upcoming sports events worldwide</div></div></div>
  <div class="toc-item" style="left:96px;top:224px"><span class="toc-num">15</span><div><div class="toc-title">Community: Building<br>the Next Generation</div><div class="toc-desc">Profiles of local clubs and programs nurturing talent and inclusion</div></div></div>
</section>

<section class="page masthead" style="left:440px;top:44px">
  <div class="head abs" style="left:9px;top:10px;font-size:19px;line-height:1">HALDEN<br>MAGAZINE</div>
  <div class="photo" role="img" aria-label="Wheelchair basketball players in an indoor gym" style="left:94px;top:8px;width:78px;height:48px;background:radial-gradient(ellipse 20% 35% at 30% 50%,#7d8fa6,transparent 70%),radial-gradient(ellipse 18% 35% at 70% 50%,#4e6ea8,transparent 70%),linear-gradient(180deg,#5a4a3c,#c9b79a 55%,#8a6f52)"></div>
  <div class="rule" style="left:9px;right:8px;top:57px"></div>
  <div class="staff" style="top:80px"><span class="role">Editor-in-Chief</span><span class="name">Mika Tanabe</span></div>
  <div class="staff" style="top:97px"><span class="role">Creative Director</span><span class="name">Rafael Moreno</span></div>
  <div class="staff" style="top:115px"><span class="role">Fashion Editor</span><span class="name">Elias Brandt</span></div>
  <div class="staff" style="top:132px"><span class="role">Beauty &amp; Wellness Editor</span><span class="name">Celine Morel</span></div>
  <div class="staff" style="top:150px"><span class="role">Writer &amp; Content Creator</span><span class="name">Ingrid Larsen</span></div>
  <div class="staff" style="top:167px"><span class="role">Photographer</span><span class="name">Lana Tran</span></div>
  <div class="photo" role="img" aria-label="Wheelchair athletes playing basketball on an outdoor court" style="left:9px;top:195px;width:78px;height:51px;background:radial-gradient(ellipse 20% 30% at 50% 55%,#5a6a86,transparent 70%),linear-gradient(180deg,#eee9df,#b7c3c9 50%,#5fa3c4)"></div>
  <div class="icon-box" style="left:93px;top:196px"><svg width="6" height="6" viewBox="0 0 10 10"><path d="M1 5 5 1.5 9 5M2.5 4v4.5h5V4" fill="none" stroke="#231f20" stroke-width="1.2"/></svg></div>
  <div class="tiny abs" style="left:107px;top:196px;font-size:2.6px">ADDRESS</div>
  <div class="tiny abs" style="left:107px;top:201px;font-size:3.4px">48 RIVERSIDE AVE., ANY CITY</div>
  <div class="icon-box" style="left:93px;top:212px"><svg width="6" height="6" viewBox="0 0 10 10"><circle cx="5" cy="5" r="4" fill="none" stroke="#231f20" stroke-width="1"/><path d="M1 5h8M5 1c-2 2.5-2 5.5 0 8M5 1c2 2.5 2 5.5 0 8" fill="none" stroke="#231f20" stroke-width=".8"/></svg></div>
  <div class="tiny abs" style="left:107px;top:212px;font-size:2.6px">WEBSITE</div>
  <div class="tiny abs" style="left:107px;top:217px;font-size:3.4px">WWW.HALDENMAG.COM</div>
</section>

<section class="page editor" style="left:641px;top:44px">
  <div class="abs" style="left:9px;top:8px;width:27px;height:27px;background:var(--lime)"></div>
  <div class="tiny abs" style="left:9px;top:18px;width:27px;text-align:center;font-size:2.6px">HALDEN<br>MAGAZINE</div>
  <div class="head abs" style="right:9px;top:10px;font-size:19px">EDITOR NOTES</div>
  <div class="rule" style="left:36px;right:9px;top:33px"></div>
  <div class="photo" role="img" aria-label="Wheelchair basketball player shooting the ball" style="left:9px;top:51px;width:65px;height:195px;background:radial-gradient(ellipse 35% 25% at 45% 45%,#8c8f92,transparent 70%),radial-gradient(ellipse 40% 15% at 50% 85%,#b3544a,transparent 70%),linear-gradient(180deg,#7fb3d8,#7c8a94 40%,#8d7560 78%,#5d4a3d)"></div>
  <div class="head abs ital" style="left:83px;top:52px;font-size:6.2px">WELCOME TO HALDEN MAGAZINE</div>
  <p class="body abs" style="left:83px;top:63px;width:88px">Welcome to a new season of stories. In these pages we meet athletes who push past limits, coaches who open doors and fans who fill the stands. Every feature is built to inform, to inspire and to remind us that sport belongs to everyone who wants to play it, on any court and in any city.</p>
  <p class="body abs" style="left:83px;top:102px;width:88px">This issue looks at new technology, smarter training and the people behind each result. We spent months on courts, tracks and in gyms to bring back honest voices. Some stories are about medals, others about the first time someone rolled onto a court and felt at home there, among friends and rivals who soon became teammates.</p>
  <p class="body abs" style="left:83px;top:146px;width:88px">Thank you for reading, sharing and joining us. Tell us which story moved you most, and which voices you want to hear next season. We are listening, and we are just getting started on a long road together.</p>
  <div class="body abs" style="left:83px;top:200px">Editor-in-Chief</div>
</section>

<section class="page feature" style="left:48px;top:329px">
  <div class="head abs" style="left:9px;top:14px;font-size:19.5px;line-height:.98">THE<br>FUTURE<br>OF<br>SPORTS</div>
  <div class="photo" role="img" aria-label="Badminton player in a sports wheelchair on an indoor court" style="left:81px;top:14px;width:90px;height:106px;background:radial-gradient(ellipse 25% 35% at 45% 45%,#5a5a3a,transparent 70%),linear-gradient(170deg,#3b2a1f,#8b6a45 50%,#c9a47a)"></div>
  <div class="tiny abs" style="left:9px;top:98px;font-size:3.4px">INNOVATIONS IN SPORTS<br>TECHNOLOGY AND TRAINING ARE<br>TRANSFORMING PERFORMANCE<br>AND ENGAGEMENT</div>
  <p class="body abs" style="left:9px;top:125px;width:76px">New chairs, lighter blades and smarter data are changing how athletes train and compete. Coaches now track every push and stride, while designers build gear around each body rather than forcing bodies to fit the gear. The result is faster times, fewer injuries and more people who can take part from their very first day.</p>
  <p class="body abs" style="left:9px;top:184px;width:76px">Clubs are also rethinking the fan side of the game. Accessible seating, live captions and audio description bring more supporters into the stands. When the crowd reflects the athletes on the court, the whole sport grows stronger and louder.</p>
  <p class="body abs" style="left:95px;top:125px;width:76px">Wearable sensors give athletes instant feedback on load, heart rate and recovery. Teams share this data with physios so plans can change the same day. The best programs mix these numbers with simple conversations about how a player feels, sleeps and eats across a long season.</p>
  <p class="body abs" style="left:95px;top:184px;width:76px">Looking ahead, the biggest change may be cultural. Young players now grow up seeing adaptive sport on screens and in schools, and they expect equal access as a given rather than a favour.</p>
  <div class="foot"></div><div class="folio">05</div>
</section>

<section class="page feature-photo" style="left:244px;top:329px">
  <div class="head abs" style="left:109px;top:13px;font-size:6.4px">TRANSFORMING<br>ATHLETE PERFORMANCE<br>AND FAN ENGAGEMENT</div>
  <div class="tiny abs" style="left:9px;top:33px;font-size:2.4px">PHOTOGRAPHY BY LANA TRAN</div>
  <div class="photo" role="img" aria-label="Two wheelchair basketball players reaching for the ball outdoors" style="left:9px;top:46px;width:162px;height:106px;background:radial-gradient(ellipse 15% 30% at 35% 55%,#8a8c90,transparent 70%),radial-gradient(ellipse 15% 30% at 68% 55%,#4e6a94,transparent 70%),radial-gradient(ellipse 25% 25% at 85% 15%,#f1d98a,transparent 70%),linear-gradient(180deg,#4d6b3a,#9bb071 45%,#8a8a86 75%,#6f6f6c)"></div>
  <p class="body abs" style="left:9px;top:160px;width:76px">Outdoor courts are where many players first try the game. Local leagues now lend chairs for free, so cost is no longer the first barrier. Volunteers run open sessions every weekend and keep the pace friendly for newcomers and returning players alike.</p>
  <p class="body abs" style="left:95px;top:160px;width:76px">Fans follow these stories online too. Short clips and live streams bring weekend games to thousands of viewers, and sponsors are starting to notice. More visibility means more funding for coaching, travel and equipment in every region.</p>
  <div class="foot"></div><div class="folio">06</div>
</section>

<section class="page interview" style="left:440px;top:329px">
  <div class="head abs" style="left:9px;top:18px;font-size:12.6px">INSIDE THE MIND OF A CHAMPION</div>
  <div class="photo" role="img" aria-label="Basketball player with a leg prosthesis dribbling on an outdoor court at sunset" style="left:9px;top:39px;width:81px;height:186px;background:radial-gradient(ellipse 30% 40% at 45% 45%,#3c4250,transparent 70%),linear-gradient(180deg,#f0dcbd,#c7a37f 40%,#6f7258 62%,#9c8a78)"></div>
  <div class="abs" style="left:97px;top:42px;width:1.5px;height:30px;background:var(--lime)"></div>
  <div class="head abs ital" style="left:102px;top:42px;font-size:6.6px">INTERVIEW<br>LEONA MARSH</div>
  <div class="tiny abs" style="left:102px;top:61px;font-size:2.4px">BY MIKA TANABE<br>PHOTOGRAPHY BY LANA TRAN</div>
  <p class="body abs" style="left:97px;top:83px;width:74px">She started playing at the local court with borrowed shoes and a second-hand blade. Today she leads her national side and mentors younger players on the road. We sat down to talk about pressure, patience and the small habits that keep her sharp between tournaments and long seasons of travel.</p>
  <div class="head abs" style="left:97px;top:146px;font-size:6px">CAN YOU TELL US<br>ABOUT YOUR JOURNEY<br>INTO THE SPORT?</div>
  <p class="body abs" style="left:97px;top:170px;width:74px">A coach saw me shooting alone one evening and asked me to join practice. I said no three times. The fourth time I went, and I have not missed a session since that night.</p>
  <div class="foot"></div><div class="folio">07</div>
</section>

<section class="page qa" style="left:641px;top:329px">
  <div class="head abs q" style="left:9px;top:18px">COULD YOU GIVE US A<br>GLIMPSE INTO YOUR<br>TRAINING ROUTINE?</div>
  <p class="body abs" style="left:80px;top:18px;width:91px">Mornings are for mobility and shooting drills, afternoons for strength and film. I keep one full day off each week, no matter what the schedule says.</p>
  <div class="rule" style="left:9px;right:9px;top:48px"></div>
  <div class="head abs q" style="left:9px;top:57px">THE MOST INFLUENTIAL<br>PERSON IN YOUR<br>SPORTING CAREER?</div>
  <p class="body abs" style="left:9px;top:86px;width:63px">My first coach. She never treated my leg as a limit, only as a detail. She pushed me on footwork and taught me to read the game two passes ahead. Most of what I teach younger players today came from her, word for word, drill for drill, including the patience it takes.</p>
  <div class="photo" role="img" aria-label="Table tennis player in a wheelchair returning a shot" style="left:80px;top:57px;width:91px;height:91px;background:radial-gradient(ellipse 30% 30% at 55% 60%,#3a3a44,transparent 70%),linear-gradient(150deg,#f1e7f4,#b7a3c9 40%,#4a8fc7 75%,#2f6fa8)"></div>
  <div class="rule" style="left:9px;right:9px;top:157px"></div>
  <div class="photo" role="img" aria-label="Wheelchair table tennis player mid-rally" style="left:9px;top:166px;width:60px;height:61px;background:radial-gradient(ellipse 30% 30% at 45% 60%,#3a3a44,transparent 70%),linear-gradient(150deg,#e9e0ee,#9d8fb3 45%,#3f86c2)"></div>
  <div class="head abs q" style="left:80px;top:168px">WHAT ARE YOUR GOALS FOR<br>THE NEXT SEASON OR YEAR?</div>
  <p class="body abs" style="left:80px;top:184px;width:91px">Win the regional title, then help launch a youth program in my home town. I want kids to find the court the way I did, only sooner and with better shoes.</p>
  <div class="foot"></div><div class="folio">08</div>
</section>

<section class="page tips" style="left:48px;top:607px">
  <div class="photo" role="img" aria-label="Sprinter with a running prosthesis exploding out of the starting blocks in a stadium" style="left:9px;top:11px;width:162px;height:162px;background:radial-gradient(ellipse 28% 35% at 65% 45%,#2a2a2a,transparent 70%),linear-gradient(180deg,#9a9a96,#6f6f6b 30%,#5f8a3a 58%,#c56a4a 86%,#b85a3f)"></div>
  <div class="head abs lime" style="left:16px;top:30px;font-size:18px;line-height:1">TIPS:<br>TRAIN LIKE<br>A PRO</div>
  <p class="body abs" style="left:11px;top:182px;width:120px">Good training starts with a plan that fits your body and your week. Build slowly, log every session and rest before you feel you need it. Small steady gains beat big jumps that end in injury.</p>
  <div class="abs" style="left:133px;top:182px;width:1px;height:30px;background:var(--lime)"></div>
  <div class="tiny abs" style="left:140px;top:182px;font-size:2.4px">BY MIKA TANABE<br>PHOTOGRAPHY BY<br>LANA TRAN</div>
  <div class="foot"></div><div class="folio">09</div>
</section>

<section class="page diet" style="left:244px;top:607px">
  <div class="tiny abs" style="left:9px;top:20px;font-size:3.5px">EXPERT TIPS FROM<br>ELITE COACHES AND<br>NUTRITIONISTS ON<br>WORKOUT ROUTINES,<br>DIET PLANS, AND<br>RECOVERY STRATEGIES</div>
  <p class="body abs" style="left:54px;top:18px;width:117px">Top coaches agree on a few basics: warm up every time, train with purpose and track how you recover. Mix strength, speed and skill work across the week so no single area is overloaded.</p>
  <p class="body abs" style="left:54px;top:44px;width:117px">Nutrition matters just as much. Eat regular meals with protein and carbs around sessions, drink water through the day and keep snacks simple. Sleep is the cheapest recovery tool you have, so protect it.</p>
  <div class="tiny abs" style="left:9px;top:156px;font-size:2.4px">BY MIKA TANABE<br>PHOTOGRAPHY BY<br>LANA TRAN</div>
  <div class="photo" role="img" aria-label="Wheelchair racers on a red running track" style="left:54px;top:91px;width:117px;height:80px;background:radial-gradient(ellipse 25% 30% at 55% 45%,#9a2f3a,transparent 70%),linear-gradient(180deg,#5c6a4a,#8a8a7a 25%,#c86a55 55%,#b9533f)"></div>
  <div class="rule" style="left:9px;right:9px;top:181px"></div>
  <div class="head abs ital" style="left:9px;top:192px;font-size:6.4px">DIET PLANS &amp;<br>RECOVERY<br>STRATEGIES</div>
  <p class="body abs" style="left:54px;top:192px;width:117px">After hard days, plan an easy one. Stretch, roll and eat within an hour of training. Listen to small aches early, and talk to your physio before they turn into long breaks from the sport.</p>
  <div class="foot"></div><div class="folio">10</div>
</section>

<section class="page tech" style="left:440px;top:607px">
  <div class="head abs" style="left:9px;top:14px;font-size:19.5px;line-height:.98">TECHNOLOGY:<br>SUPER SHOE<br>INNOVATIONS</div>
  <div class="tiny abs" style="left:114px;top:66px;font-size:2.4px">BY MIKA TANABE<br>PHOTOGRAPHY BY LANA TRAN</div>
  <div class="photo" role="img" aria-label="Sprinter crouched at the start line on a red track" style="left:9px;top:82px;width:96px;height:173px;background:radial-gradient(ellipse 35% 25% at 50% 50%,#3a3028,transparent 70%),linear-gradient(180deg,#c96a50,#b5523b 60%,#a8492f)"></div>
  <div class="photo" role="img" aria-label="Smiling wheelchair racer on a track wearing a race bib" style="left:114px;top:82px;width:57px;height:96px;background:linear-gradient(180deg,#d9d4cc,#a33a3a 45%,#3a9a8a 75%,#222)"></div>
  <div class="head abs ital" style="left:114px;top:188px;font-size:6.2px">HALDEN PINK ULTRA</div>
  <div class="tiny abs" style="left:114px;top:198px;font-size:2.4px">SUPER SHOES DESIGNED FOR PROFESSIONAL<br>FEMALE ATHLETES, DEVELOPED BY HALDEN<br>COMPANY SINCE 2016</div>
  <div class="foot" style="left:105px"></div><div class="folio">11</div>
</section>

<section class="page speed" style="left:641px;top:607px">
  <div class="head abs q" style="left:9px;top:22px">UNMATCHED SPEED<br>AND PERFORMANCE<br>FOR EVERY ATHLETE</div>
  <p class="body abs" style="left:80px;top:20px;width:91px">Each pair is tuned for grip, bounce and balance, so athletes can focus on the race rather than on their feet.</p>
  <div class="rule" style="left:9px;right:9px;top:50px"></div>
  <div class="head abs q" style="left:9px;top:61px">TECHNOLOGY<br>&amp; MATERIAL</div>
  <div class="tiny abs" style="left:9px;top:77px;font-size:2.3px">FEATURE CUTTING-EDGE DESIGN FOR<br>ATHLETES, OFFERING ENHANCED SPEED,<br>COMFORT, AND SUPPORT TO MAXIMIZE<br>PERFORMANCE AND REDUCE FATIGUE</div>
  <p class="body abs" style="left:9px;top:95px;width:63px">A light carbon plate adds spring at toe-off while a soft foam layer protects joints on long runs. The upper is knit for airflow and shaped to fit both feet and running blades, with laces that lock in place during sharp turns and hard finishes.</p>
  <div class="photo" role="img" aria-label="Athlete with a leg prosthesis climbing stadium stairs" style="left:80px;top:57px;width:91px;height:104px;background:radial-gradient(ellipse 25% 30% at 50% 30%,#2a2a2e,transparent 70%),linear-gradient(180deg,#e6e8ea,#b9c0c6 35%,#c2562e 70%,#3a3a3a)"></div>
  <div class="rule" style="left:9px;right:9px;top:175px"></div>
  <div class="tiny abs" style="left:9px;top:186px;font-size:2.4px">BY MIKA TANABE<br>PHOTOGRAPHY BY LANA TRAN</div>
  <p class="body abs" style="left:77px;top:184px;width:94px">Field tests ran for a full season with club and elite athletes, and their notes shaped every change to the final design.</p>
  <div class="foot"></div><div class="folio">12</div>
</section>

<section class="page subscribe" style="left:48px;top:885px">
  <div class="head abs" style="left:0;right:0;top:10px;text-align:center;font-size:19px">SUBSCRIBE US</div>
  <div class="rule" style="left:9px;right:13px;top:33px"></div>
  <div class="photo" role="img" aria-label="Wheelchair basketball game in an indoor arena" style="left:9px;top:35px;width:158px;height:105px;background:radial-gradient(ellipse 15% 30% at 30% 50%,#d8d3cc,transparent 70%),radial-gradient(ellipse 15% 30% at 62% 50%,#b53a36,transparent 70%),linear-gradient(180deg,#4a3a2e,#8a6a4a 45%,#6a4a35 80%,#3e2e24)"></div>
  <div class="head abs" style="left:9px;top:158px;font-size:18px">NEVER MISS AN ISSUE!</div>
  <div class="rule" style="left:9px;right:9px;top:185px"></div>
  <div class="head abs ital" style="left:9px;top:198px;font-size:6.2px">50% OFF<br>FOR YEARLY<br>SUBSCRIPTION</div>
  <p class="body abs" style="left:72px;top:198px;width:99px;font-size:2.9px;text-align:left">Stay ahead of the sports curve with a subscription to Brookfield Magazine. Enjoy exclusive content, early access to new issues, and special subscriber-only perks. Visit our website to subscribe now and never miss an issue!</p>
  <div class="tiny abs" style="left:72px;top:232px;font-size:3px">WWW.HALDENMAG.COM</div>
</section>

<section class="page back-cover" style="left:244px;top:885px">
  <div class="photo" role="img" aria-label="Sprinter crouched in the start position on a red running track" style="inset:0;background:radial-gradient(ellipse 35% 30% at 50% 40%,#3a3028,transparent 70%),linear-gradient(180deg,#c9735a,#b85a42 50%,#a6493a)"></div>
  <div class="head abs lime" style="left:0;right:0;top:200px;text-align:center;font-size:16px;line-height:1.05">GEAR UP. PLAY BOLD.<br>PERFORM BEYOND.</div>
</section>

</main>
</body>
</html>
```